Wedding Videography Wordpress Website Theme

We need a modern and high-end website look for our wedding video and film business. We film weddings all over the United Kingdom and at European destinations so need something to reflect our work. The website should be visually stunning with images and videos being the focal point as this is what our services are.

The current website is www.brunolessway.com so you will be able to see our brand.

My Instagram is www.instagram.com/brunolesswayfilms so a new design should link in with this idea.

We need the following pages designed by the winning designer

1 - Homepage
2 - Films Index Page
3 - Testimonials
4 - Prices
5 - Reviews
6 - Meet Bruno (About)
7 - Contact
8 - Blog Index
9 - Blog Page

All pages must be consistent so have a similar style.

Pages on menu:
Meet Bruno
Videos
Packages
Testimionials
Journal (Blog)
Contact

We require a responsive look too. Over 90% of our visitors access the website via their mobile devices.

```html
<!DOCTYPE html>
<html lang="en">
<head>
<meta charset="utf-8">
<title>Bruno Lessway Wedding Films</title>
<link href="https://fonts.googleapis.com/css2?family=Montserrat:wght@400;500;600;700;800&family=Open+Sans:wght@400;600&display=swap" rel="stylesheet">
<style>
:root{
  --gold:#9c8752;
  --gold-dark:#7e6a3a;
  --gold-light:#b9a46c;
  --ink:#1d1d1d;
  --text:#555;
  --mist:#e6ebe8;
  --white:#fff;
  --black:#0b0b0b;
}
*{box-sizing:border-box;margin:0;padding:0}
html,body{width:1200px;height:4932px;overflow:hidden}
body{font-family:"Open Sans",Arial,sans-serif;color:var(--text);background:var(--white);position:relative}
h1,h2,h3,h4,.nav,.btn,.brand{font-family:"Montserrat",Arial,sans-serif}
.abs{position:absolute}

/* hero */
.hero{position:absolute;left:0;top:0;width:1200px;height:680px;
  background:radial-gradient(ellipse at 55% 45%,#b8a995 0%,#6f6558 45%,#2f2a25 100%);}
.hero-shade{position:absolute;inset:0;background:linear-gradient(180deg,rgba(0,0,0,.35),rgba(0,0,0,.1) 40%,rgba(0,0,0,.45))}
.nav{position:absolute;top:44px;font-size:13px;font-weight:500;color:var(--white);letter-spacing:.5px;display:flex;gap:26px;text-transform:uppercase}
.nav.left{left:140px}.nav.right{right:140px}
.nav .current{color:var(--gold-light)}
.brand{position:absolute;left:0;width:1200px;top:36px;text-align:center;color:var(--white)}
.brand .mark{display:block;width:28px;height:28px;border:2px solid var(--white);border-radius:50%;margin:0 auto 6px}
.brand .name{font-size:18px;font-weight:600;letter-spacing:4px}
.brand .sub{font-size:8px;letter-spacing:4px;font-weight:500}
.hero h1{position:absolute;top:282px;width:1200px;text-align:center;color:var(--white);font-size:52px;font-weight:600;letter-spacing:3px}
.hero .tag{position:absolute;top:356px;width:1200px;text-align:center;color:var(--white);font-family:"Montserrat",sans-serif;font-size:15px;font-weight:700;letter-spacing:1px}
.play{position:absolute;width:56px;height:56px;border-radius:50%;background:var(--gold);display:flex;align-items:center;justify-content:center}
.play.white{background:var(--white)}

/* latest */
.latest-band{position:absolute;left:0;top:680px;width:1200px;height:340px;background:var(--mist)}
.section-title{position:absolute;width:1200px;text-align:center;color:var(--ink);font-size:38px;font-weight:700;letter-spacing:3px}
.rule{position:absolute;height:3px;background:var(--gold)}
.media{position:absolute;box-shadow:0 18px 30px rgba(0,0,0,.3)}
.latest-film{left:120px;top:900px;width:960px;height:260px;background:radial-gradient(ellipse at 50% 50%,#6d7670,#2d332f 70%,#1a1d1b)}

.triangle{position:absolute;width:0;height:0;border-left:14px solid transparent;border-right:14px solid transparent;border-bottom:22px solid var(--gold-light)}

.frame{position:absolute;border:6px solid var(--gold-dark)}

h2.feature{position:absolute;color:var(--ink);font-size:31px;font-weight:800;line-height:1.22;letter-spacing:.5px;text-transform:uppercase}
h2.feature.small{font-size:24px;line-height:1.3}
.copy{position:absolute;font-size:13px;line-height:1.75;color:#666}
.copy p{margin-bottom:16px}
.btn{position:absolute;font-size:12px;font-weight:600;color:var(--gold-dark);border:2px solid var(--gold-dark);padding:10px 16px;letter-spacing:.5px;text-transform:uppercase;background:var(--white)}

/* drone */
.drone{position:absolute;left:0;top:2488px;width:1200px;height:472px;
  background:linear-gradient(90deg,#262a24 0%,#4d5445 30%,#6a7260 50%,#3f4637 75%,#1c1f1a 100%)}
.drone h2{position:absolute;top:176px;width:1200px;text-align:center;color:var(--white);font-size:40px;font-weight:600;letter-spacing:2px}
.drone .caption{position:absolute;top:236px;left:640px;color:rgba(255,255,255,.6);font-family:"Montserrat",sans-serif;font-size:17px;letter-spacing:5px}

/* testimonial */
.kicker{position:absolute;width:1200px;text-align:center;color:var(--ink);font-family:"Montserrat",sans-serif;font-size:12px;font-weight:700;letter-spacing:.5px;text-transform:uppercase}
.couple{position:absolute;top:3080px;width:1200px;text-align:center;color:var(--ink);font-size:46px;font-weight:700;letter-spacing:2px}
.quote{position:absolute;left:200px;width:800px;top:3148px;text-align:center;color:#444;font-size:13px;line-height:1.6;text-transform:uppercase}
.venue{position:absolute;top:3240px;width:1200px;text-align:center;color:var(--ink);font-family:"Montserrat",sans-serif;font-size:12px;font-weight:700;text-transform:uppercase}
.testimonial-film{left:120px;top:3300px;width:960px;height:380px;background:linear-gradient(90deg,#121418 0%,#3b3f46 40%,#8a8e92 60%,#e8e8e8 100%)}

/* contact */
.contact-photo{left:120px;top:3788px;width:420px;height:372px;background:radial-gradient(ellipse at 40% 40%,#8e8d86,#3b3a36 60%,#141414)}
h2.contact-title{position:absolute;left:620px;top:3844px;color:var(--ink);font-size:32px;font-weight:800;letter-spacing:1px}

/* brochure */
.brochure{position:absolute;left:0;top:4260px;width:1200px;height:188px;background:linear-gradient(90deg,#7f6c3e,#a8945d 50%,#7f6c3e)}
.brochure h2{position:absolute;top:70px;width:1200px;text-align:center;color:var(--white);font-size:36px;font-weight:800;letter-spacing:1px;text-transform:uppercase}

/* footer */
.footer{position:absolute;left:0;top:4448px;width:1200px;height:484px;background:var(--black);color:var(--white)}
.newsletter{position:absolute;left:376px;top:88px;width:452px;height:40px;border-radius:20px;background:var(--white);display:flex;align-items:center;justify-content:space-between;padding-left:20px}
.newsletter span{font-size:12px;color:#888}
.newsletter b{height:40px;border-radius:20px;background:var(--gold);color:var(--white);font-family:"Montserrat",sans-serif;font-size:12px;font-weight:700;padding:0 26px;display:flex;align-items:center}
.col{position:absolute;top:180px}
.col h4{font-size:24px;font-weight:600;margin-bottom:16px}
.col li{list-style:none;font-size:14px;line-height:1.9;color:#ddd}
.divider{position:absolute;top:180px;width:1px;height:160px;background:#555}
.contact-line{display:flex;gap:12px;align-items:flex-start;font-size:13px;line-height:1.5;color:#ddd;margin-bottom:10px}
.socials{display:flex;gap:10px}
.socials i{width:34px;height:34px;border:1.5px solid var(--white);border-radius:50%;display:block}
.copyright{position:absolute;top:448px;width:1200px;text-align:center;font-size:13px;color:#ddd}
</style>
</head>
<body>

<header class="hero" role="img" aria-label="Photo of a smiling bride and groom walking through confetti">
  <div class="hero-shade"></div>
  <nav class="nav left"><span class="current">Home</span><span>Meet Bruno</span><span>Videos</span><span>Packages</span></nav>
  <div class="brand"><span class="mark"></span><div class="name">BRUNO LESSWAY</div><div class="sub">WEDDING FILMS</div></div>
  <nav class="nav right"><span>Testimonials</span><span>Journal</span><span>Enquire</span></nav>
  <h1>BRUNO LESSWAY</h1>
  <div class="tag">NORTH EAST AND YORKSHIRE WEDDING VIDEOGRAPHER</div>
  <div class="play" style="left:572px;top:392px"><svg width="18" height="20"><path d="M2 1 L17 10 L2 19 Z" fill="#fff"/></svg></div>
</header>

<section aria-label="Latest wedding">
  <div class="latest-band"></div>
  <h2 class="section-title" style="top:776px">LATEST WEDDING</h2>
  <div class="rule" style="left:540px;top:838px;width:120px"></div>
  <div class="media latest-film" role="img" aria-label="Video still of a groom and bride under falling confetti"></div>
  <div class="play white" style="left:572px;top:1000px"><svg width="18" height="20"><path d="M2 1 L17 10 L2 19 Z" fill="#9c8752"/></svg></div>
</section>

<section aria-label="Your wedding day">
  <div class="triangle" style="left:586px;top:1330px"></div>
  <div class="frame" style="left:128px;top:1380px;width:310px;height:330px"></div>
  <div class="media" style="left:150px;top:1400px;width:276px;height:296px;background:linear-gradient(160deg,#d4c29b,#8d7d5e 55%,#4e4a3d)" role="img" aria-label="Photo of a couple embracing in a sunlit field"></div>
  <h2 class="feature" style="left:580px;top:1374px;width:520px">Your wedding day<br>is the most important<br>day of your life...</h2>
  <div class="rule" style="left:580px;top:1536px;width:110px;height:2px"></div>
  <div class="copy" style="left:580px;top:1566px;width:500px">
    <p>The celebration of your love story, and you'll want to remember it for the rest of your lives. Your wedding film is the best way to keep this day alive forever, a newlywed's gift that keeps giving, an infinite reminder of those special moments and memories.</p>
    <p>Everything about your wedding day belongs to you, the couple. Your story. Your vibe. Your friends and family. Your pre-wedding jitters. Your tears. Your laughter. Your vows. Your excitement. Your first dance. Everything. And I'm passionate about creating a wedding film that captures the very essence of your day and turning it into a family heirloom you'll treasure forever.</p>
  </div>
</section>

<section aria-label="About Bruno">
  <div class="triangle" style="left:120px;top:1874px"></div>
  <h2 class="feature small" style="left:120px;top:1924px;width:480px">Bruno Lessway, a trusted and acclaimed wedding filmmaker based in the North East and Yorkshire, has more than 20 years of filmmaking experience.</h2>
  <div class="copy" style="left:120px;top:2132px;width:470px">
    <p>From beautiful barns and luxurious country hotels to sun-drenched Greek islands and ancient Italian abbeys, he has filmed all kinds of unforgettable weddings.</p>
    <p>If you're looking for a highly experienced wedding videographer who focuses on your story, the groundswell moments and the emotions filling the room as you enter, get in touch with Bruno today.</p>
  </div>
  <div class="btn" style="left:120px;top:2340px">Learn more →</div>
  <div class="frame" style="left:676px;top:1926px;width:392px;height:450px"></div>
  <div class="media" style="left:658px;top:1908px;width:392px;height:450px;background:radial-gradient(ellipse at 40% 55%,#a0a198,#4c4f43 60%,#22241e)" role="img" aria-label="Aerial photo of a bride and groom on a lawn"></div>
</section>

<section class="drone" role="img" aria-label="Aerial drone view over a garden venue">
  <h2>LICENCED DRONE PILOT</h2>
  <div class="caption">BRUNO LESSWAY WEDDING FILMS</div>
  <div class="play white" style="left:572px;top:244px"><svg width="18" height="20"><path d="M2 1 L17 10 L2 19 Z" fill="#9c8752"/></svg></div>
</section>

<section aria-label="Testimonial">
  <div class="kicker" style="top:3040px">North East &amp; Yorkshire Wedding Videographer Video Testimonial</div>
  <h2 class="couple">AMARA + LEO</h2>
  <p class="quote">"We have a really emotional video for our wedding, it is a beauty video that is going to stay with us for the rest of our lives. Bruno was everywhere but you couldn't tell he was there, he was a really fun guy and we now consider him a friend"</p>
  <div class="venue">Married at Villa Corvina, Umbria, Italy</div>
  <div class="media testimonial-film" role="img" aria-label="Video still of a groom in a tuxedo and a bride with a bouquet"></div>
</section>

<section aria-label="Get in touch">
  <div class="media contact-photo" role="img" aria-label="Photo of a couple silhouetted against soft evening light"></div>
  <div class="triangle" style="left:620px;top:3800px"></div>
  <h2 class="contact-title">GET IN TOUCH</h2>
  <div class="rule" style="left:620px;top:3896px;width:110px;height:2px"></div>
  <div class="copy" style="left:620px;top:3920px;width:460px">
    <p>Bruno works with a limited number of couples every year, so if you're looking for a friendly, professional wedding filmmaker in the North East and Yorkshire region, who will exceed your expectations, take that first step today.</p>
    <p>Complete the enquiry form or take a look at more of Bruno's breathtaking wedding videos and 5* feedback on his social page.</p>
  </div>
  <div class="btn" style="left:620px;top:4112px">Contact us</div>
</section>

<section class="brochure"><h2>Download my wedding video brochure</h2></section>

<footer class="footer">
  <div class="newsletter"><span>Email address</span><b>SUBSCRIBE</b></div>
  <div class="col" style="left:136px">
    <h4>Links</h4>
    <ul><li>FAQ's</li><li>Wedding Photography</li><li>Commercial</li><li>North East Wedding</li></ul>
  </div>
  <div class="divider" style="left:340px"></div>
  <div class="col" style="left:460px">
    <h4>Contact us</h4>
    <div class="contact-line"><svg width="12" height="16"><path d="M6 1a5 5 0 0 1 5 5c0 4-5 9-5 9S1 10 1 6a5 5 0 0 1 5-5z" fill="#fff"/><circle cx="6" cy="6" r="2" fill="#000"/></svg><span>12 Linden Court, Market Row,<br>Harrowgate Lane</span></div>
    <div class="contact-line"><svg width="14" height="14"><path d="M3 1l3 3-2 2c1 2 2 3 4 4l2-2 3 3-2 2C6 13 1 8 1 3z" fill="#fff"/></svg><span>07700 900 123</span></div>
    <div class="contact-line"><svg width="14" height="12"><rect x="1" y="1" width="12" height="10" fill="none" stroke="#fff"/><path d="M1 1l6 5 6-5" fill="none" stroke="#fff"/></svg><span>films@brunolessway.com</span></div>
  </div>
  <div class="divider" style="left:840px"></div>
  <div class="col" style="left:916px">
    <h4>Follow us</h4>
    <div class="socials"><i></i><i></i><i></i><i></i></div>
  </div>
  <div class="copyright">© Copyrights 2023 The Company Name All Rights Reserved</div>
</footer>

</body>
</html>
```